Website for enterprise software start-up

We need a new Wordpress website. We are an early stage start-up focused on mobile video technology for cellular operators. The audience is strategy, marketing and customer acquisition execs from the operators.

The purpose of the site is to act as a sales brochure and capture leads. A demo app can be downloaded from the current site, want to put that behind a contact form.

Current website is at www.velmora.tv. Similar number of pages. Looking for a clean design template, with minimal customization. Blog will remain as is.

Want to be able to modify the copy via Wordpress. Reference designs I like: quandrix.com, briskfold7metrics.com

Target Market(s)

Mobile operators and MVNOs in the US and Asia Pacific regions

Industry/Entity Type

Business Software

Coding

Coded - Design and coding required

Number of Pages Required

4 page

Font styles to use
Sans Serif

Colors
f78f20

Requirements
Must have
• Form for downloading sample apps.
• Landing page with image, Product, Blog, About, Contact
• Team page

```html
<!DOCTYPE html>
<html lang="en">
<head>
<meta charset="utf-8">
<title>Velmora Media</title>
<link href="https://fonts.googleapis.com/css2?family=Ubuntu:wght@400;500;700&family=Open+Sans:ital,wght@0,400;0,600;1,400&display=swap" rel="stylesheet">
<style>
:root{
  --orange:#df7416;
  --orange-soft:#e8883a;
  --ink:#2b2b2b;
  --body:#6a6a6a;
  --muted:#9a9a9a;
  --line:#e2e2e2;
  --grey-band:#f0f0f0;
  --white:#ffffff;
  --dark:#222222;
}
*{margin:0;padding:0;box-sizing:border-box}
html,body{width:1200px;height:2699px;overflow:hidden;background:var(--white)}
body{position:relative;font-family:"Open Sans",Arial,sans-serif;color:var(--body)}
.abs{position:absolute}
h1,h2,h3,.brand,.nav a,.heading{font-family:"Ubuntu","Open Sans",sans-serif}

/* header */
.site-header{position:absolute;left:0;top:0;width:1200px;height:82px;background:var(--white);border-bottom:1px solid var(--line)}
.brand{position:absolute;display:flex;align-items:center;gap:10px;font-weight:700;color:var(--ink)}
.brand .mark{background:var(--orange);display:block}
.site-header .brand{left:162px;top:18px;font-size:38px}
.site-header .brand .mark{width:42px;height:42px}
.nav{position:absolute;left:578px;top:34px;display:flex}
.nav a{font-size:11px;color:var(--ink);text-decoration:none;letter-spacing:.3px;margin-right:38px}
.nav a.active{color:var(--orange)}
.btn{position:absolute;background:var(--orange);color:var(--white);font-size:12px;display:flex;align-items:center;justify-content:center;gap:10px;border-radius:2px}
.btn .tri{width:0;height:0;border-left:7px solid var(--white);border-top:5px solid transparent;border-bottom:5px solid transparent}
.login{left:968px;top:29px;width:70px;height:26px;font-size:11px}

/* hero */
.hero{position:absolute;left:0;top:82px;width:1200px;height:526px;
  background:
    radial-gradient(ellipse 260px 330px at 230px 330px,rgba(70,45,30,.75),rgba(70,45,30,0) 70%),
    radial-gradient(ellipse 160px 240px at 560px 240px,rgba(240,240,236,.9),rgba(240,240,236,0) 70%),
    radial-gradient(ellipse 120px 200px at 470px 380px,rgba(205,160,130,.8),rgba(205,160,130,0) 70%),
    linear-gradient(100deg,#8a6a52 0%,#c9a98c 22%,#ece0cf 45%,#f2ece4 65%,#ddd3c7 85%,#cbbfb1 100%)}
.hero-title{position:absolute;right:178px;top:168px;text-align:right;color:var(--dark);font-family:"Ubuntu",sans-serif;font-weight:400;font-size:36px;line-height:41px}
.hero-sub{position:absolute;right:178px;top:255px;width:270px;text-align:right;font-size:10.5px;line-height:14px;color:#333}
.store{position:absolute;top:294px;height:33px;width:108px;background:#111;border-radius:4px;border:1px solid #666;color:#fff;display:flex;flex-direction:column;justify-content:center;padding-left:30px;font-family:"Open Sans",sans-serif}
.store small{font-size:7px;line-height:8px;text-transform:uppercase;letter-spacing:.2px}
.store b{font-size:13px;line-height:15px;font-weight:600}
.store::before{content:"";position:absolute;left:9px;top:9px;width:14px;height:14px;border-radius:3px;background:#fff}
.sample{left:900px;top:294px;width:123px;height:33px}
.arrow{position:absolute}

/* about */
.vert{position:absolute;font-family:"Ubuntu",sans-serif;font-size:22px;color:#dedede;letter-spacing:4px;transform:rotate(90deg);transform-origin:left top;white-space:nowrap}
.about-head{position:absolute;left:162px;top:658px;display:flex;align-items:center;gap:10px;font-size:29px;color:var(--ink);font-family:"Ubuntu",sans-serif}
.about-head .brand{position:static;font-size:29px}
.about-head .brand .mark{width:32px;height:32px}
.about-text{position:absolute;left:162px;top:720px;width:575px;font-size:11px;line-height:21px}
.about-text p{margin-bottom:10px}
.read-about{left:162px;top:878px;width:113px;height:30px}

/* product */
.product{position:absolute;left:0;top:962px;width:1200px;height:476px;background:var(--orange);overflow:hidden}
.product .shade{position:absolute;background:rgba(255,255,255,.07)}
.product h2{position:absolute;left:505px;top:76px;color:var(--white);font-size:28px;font-weight:400;display:flex;align-items:center;gap:12px}
.features{position:absolute;left:507px;top:146px;width:520px;list-style:none}
.features li{position:relative;padding-left:24px;color:var(--white);font-size:12px;line-height:18px;margin-bottom:23px}
.features li svg{position:absolute;left:0;top:3px}

/* updates */
.section-title{position:absolute;left:162px;font-size:29px;color:var(--ink);font-weight:400}
.section-title span{color:var(--orange)}
.date{position:absolute;left:162px;top:1572px;width:50px;height:92px;border-right:1px solid var(--line);text-align:center}
.date b{display:block;color:var(--orange);font-size:19px;font-weight:600;margin-top:14px}
.date i{font-style:normal;font-size:11px;color:var(--ink)}
.post-title{position:absolute;left:245px;top:1556px;font-size:15px;font-weight:500;color:var(--ink)}
.post-meta{position:absolute;left:245px;top:1588px;font-size:11px;font-style:italic;color:var(--orange)}
.post-excerpt{position:absolute;left:245px;top:1609px;width:410px;font-size:11px;line-height:21px}
.read-post{left:243px;top:1684px;width:113px;height:30px}

/* team */
.team{position:absolute;left:0;top:1778px;width:1200px;height:402px;background:var(--grey-band)}
.card{position:absolute;top:106px;width:190px;height:244px;overflow:hidden}
.card.photo{background:
  radial-gradient(ellipse 55px 70px at 95px 100px,#e2b9a0,rgba(226,185,160,0) 75%),
  linear-gradient(180deg,#e9e7e3 0%,#dcd8d2 55%,#2e3440 80%,#232831 100%)}
.card .label{position:absolute;left:0;bottom:0;width:100%;height:52px;background:rgba(35,35,35,.92);color:var(--white);font-size:13px;font-weight:600;display:flex;align-items:center;justify-content:center}
.card.featured{background:var(--orange);text-align:center;color:var(--white)}
.card.featured h3{font-size:17px;font-weight:500;margin-top:36px}
.card.featured p{font-size:11px;line-height:19px;padding:8px 18px 0}
.socials{display:flex;gap:7px;justify-content:center;margin-top:14px}
.socials span{width:20px;height:20px;border-radius:50%;background:var(--white);display:block}

/* partners + contact */
.partner{position:absolute;width:110px;height:85px;border:1px solid var(--line);display:flex;align-items:center;justify-content:center;font-family:"Ubuntu",sans-serif;font-size:15px;font-weight:500;color:#a9a9a9}
.partner .emblem{width:46px;height:46px;border-radius:50%;background:#d3d3d3}
.dots span{position:absolute;width:13px;height:13px;border-radius:50%;background:#cfcfcf}
.cert{position:absolute;left:162px;top:2525px;width:194px;height:70px;border:1px solid var(--line);border-radius:8px;display:flex;align-items:center;gap:12px;padding-left:10px;background:#f6f6f6}
.cert .mark{width:54px;height:54px;background:var(--orange);border-radius:8px}
.cert .brand{position:static;font-size:22px}
.cert-note{position:absolute;left:374px;top:2538px;width:220px;font-size:11px;line-height:20px}
.cert-note a{color:var(--orange);text-decoration:none}
.field{position:absolute;left:668px;width:370px;border:1px solid var(--line);font-size:10px;color:#aaa;padding:10px 14px}
.send{left:668px;top:2563px;width:132px;height:31px}

/* footer */
.site-footer{position:absolute;left:0;top:2648px;width:1200px;height:51px;background:var(--orange);color:var(--white);font-size:10px}
.site-footer .copy{position:absolute;left:162px;top:19px}
.site-footer .follow{position:absolute;left:784px;top:18px;font-weight:600}
.site-footer .icons{position:absolute;left:855px;top:12px;display:flex;gap:10px}
.site-footer .icons span{width:27px;height:27px;border:1.5px solid var(--white);border-radius:50%;display:block}
</style>
</head>
<body>

<header class="site-header">
  <div class="brand"><span class="mark"></span>velmora</div>
  <nav class="nav">
    <a class="active" href="#">ABOUT</a><a href="#">PRODUCT</a><a href="#">OUR TEAM</a><a href="#">BLOG</a><a href="#">CONTACT</a>
  </nav>
  <div class="btn login">LOGIN <span class="tri"></span></div>
</header>

<section class="hero" role="img" aria-label="Woman holding a smartphone playing a video in a bright room">
  <svg class="arrow" style="left:94px;top:220px" width="36" height="70"><polyline points="34,2 2,35 34,68" fill="none" stroke="#fff" stroke-width="2"/></svg>
  <svg class="arrow" style="left:1072px;top:220px" width="36" height="70"><polyline points="2,2 34,35 2,68" fill="none" stroke="#fff" stroke-width="2"/></svg>
  <h1 class="hero-title">High Quality<br>Mobile Engagement™</h1>
  <p class="hero-sub">We engage mobile audiences with the right video content at the perfect moment.</p>
  <div class="store" style="left:662px"><small>Available on the</small><b>Mobile Store</b></div>
  <div class="store" style="left:781px"><small>Get it on</small><b>App Market</b></div>
  <div class="btn sample">Sample Apps <span class="tri"></span></div>
</section>

<section class="about">
  <div class="about-head"><span>We are</span><span class="brand"><span class="mark"></span>velmora</span></div>
  <div class="about-text">
    <p>Velmora Media exists because video consumption is trending away from TV towards mobile, and because mobile media is trending away from pull consumption towards push consumption - where each user is notified of personalized content at the perfect moment.</p>
    <p>We started Velmora Media to help media publishers navigate these trends, solving the technical challenges of delivering personalized and highest quality mobile video experiences, and seizing the economic opportunity of attracting premium brand advertising.</p>
  </div>
  <div class="btn read-about">Read More <span class="tri"></span></div>
  <div class="abs" role="img" aria-label="Hand holding a smartphone showing the app start screen" style="left:776px;top:643px;width:232px;height:319px;background:radial-gradient(ellipse 70px 110px at 130px 110px,#5b4a63,rgba(91,74,99,0) 80%),radial-gradient(ellipse 110px 170px at 150px 230px,#e6c1aa,rgba(230,193,170,0) 85%),linear-gradient(180deg,#fff 0%,#f4ece6 100%)"></div>
  <div class="vert" style="left:1040px;top:640px">— about —</div>
</section>

<section class="product">
  <div class="shade" style="left:-40px;top:20px;width:300px;height:60px;transform:skewX(-30deg)"></div>
  <div class="shade" style="left:700px;top:320px;width:200px;height:200px;transform:rotate(45deg)"></div>
  <svg class="abs" style="left:582px;top:0" width="36" height="16"><polygon points="0,0 36,0 18,16" fill="#fff"/></svg>
  <div class="abs" role="img" aria-label="Two smartphones showing a push video notification" style="left:216px;top:64px;width:262px;height:360px;background:radial-gradient(ellipse 90px 70px at 110px 200px,#6f7d5c,rgba(111,125,92,0) 80%),radial-gradient(ellipse 130px 170px at 110px 175px,#3b3b44,rgba(59,59,68,0) 90%),linear-gradient(180deg,rgba(240,240,240,.95),rgba(210,210,210,.95));border-radius:26px"></div>
  <div class="dots"><span style="left:164px;top:204px;background:#f0a160"></span><span style="left:162px;top:234px;width:17px;height:17px;background:#f7d3b3;border:2px solid #f0a160"></span><span style="left:164px;top:268px;background:#f0a160"></span></div>
  <h2><svg width="14" height="16"><rect x="0" y="2" width="3" height="12" fill="#fff"/><polygon points="14,0 5,8 14,16" fill="#fff"/></svg>Push Video Notifications</h2>
  <ul class="features">
    <li><svg width="12" height="12"><circle cx="6" cy="6" r="5" fill="none" stroke="#fff"/><polyline points="3.5,6 5.5,8 8.5,4" fill="none" stroke="#fff"/></svg>Personalised flawless HD videos, revealed at the perfect moment, as rich media notifications.</li>
    <li><svg width="12" height="12"><circle cx="6" cy="6" r="5" fill="none" stroke="#fff"/><polyline points="3.5,6 5.5,8 8.5,4" fill="none" stroke="#fff"/></svg>Guarantee your audience never gets frustrated with a poor quality mobile video streaming experience.</li>
    <li><svg width="12" height="12"><circle cx="6" cy="6" r="5" fill="none" stroke="#fff"/><polyline points="3.5,6 5.5,8 8.5,4" fill="none" stroke="#fff"/></svg>Instant video playback, zero buffering, HD quality guaranteed - even when offline.</li>
    <li><svg width="12" height="12"><circle cx="6" cy="6" r="5" fill="none" stroke="#fff"/><polyline points="3.5,6 5.5,8 8.5,4" fill="none" stroke="#fff"/></svg>Content is personalised based on viewer interests and mobile viewing habits.</li>
    <li><svg width="12" height="12"><circle cx="6" cy="6" r="5" fill="none" stroke="#fff"/><polyline points="3.5,6 5.5,8 8.5,4" fill="none" stroke="#fff"/></svg>Monetize with beautiful HD preroll or interstitial ads.</li>
    <li><svg width="12" height="12"><circle cx="6" cy="6" r="5" fill="none" stroke="#fff"/><polyline points="3.5,6 5.5,8 8.5,4" fill="none" stroke="#fff"/></svg>Use your existing content management and hosting systems.</li>
  </ul>
</section>

<section class="updates">
  <h2 class="section-title heading" style="top:1486px">Latest <span>Updates</span></h2>
  <svg class="arrow" style="left:108px;top:1608px" width="14" height="28"><polyline points="13,1 1,14 13,27" fill="none" stroke="#ccc" stroke-width="1.5"/></svg>
  <svg class="arrow" style="left:1078px;top:1608px" width="14" height="28"><polyline points="1,1 13,14 1,27" fill="none" stroke="#ccc" stroke-width="1.5"/></svg>
  <div class="date"><b>18</b><i>March</i></div>
  <h3 class="post-title">Closing the Gap: Smartphones vs TV</h3>
  <div class="post-meta">JUNE 26, 2016 / OWEN HALE</div>
  <p class="post-excerpt">What's the difference between mobile and television? About $22billion, at least where advertising budgets are concerned. It's known as the "Halden Gap", the difference between time audiences spend on mobile and the total...</p>
  <div class="btn read-post">Read More <span class="tri"></span></div>
  <div class="abs" role="img" aria-label="Hands holding a smartphone playing a video" style="left:695px;top:1556px;width:295px;height:170px;background:radial-gradient(ellipse 60px 80px at 80px 60px,#4a3328,rgba(74,51,40,0) 80%),radial-gradient(ellipse 40px 60px at 225px 85px,#3a3a3f,rgba(58,58,63,0) 85%),linear-gradient(110deg,#9a7b66,#d7c6b6 55%,#efe7de);box-shadow:0 1px 4px rgba(0,0,0,.25)"></div>
  <div class="vert" style="left:1040px;top:1500px">— Our Blog —</div>
</section>

<section class="team">
  <h2 class="section-title heading" style="top:48px">Management <span>Team</span></h2>
  <svg class="arrow" style="left:108px;top:206px" width="14" height="28"><polyline points="13,1 1,14 13,27" fill="none" stroke="#ccc" stroke-width="1.5"/></svg>
  <svg class="arrow" style="left:1078px;top:206px" width="14" height="28"><polyline points="1,1 13,14 1,27" fill="none" stroke="#ccc" stroke-width="1.5"/></svg>
  <div class="card photo" style="left:162px" role="img" aria-label="Portrait of the company CEO"><div class="label">Company CEO - Owen</div></div>
  <div class="card featured" style="left:376px">
    <h3>Lars</h3>
    <p>Leads engineering and product delivery, building fast video tools for mobile operators across many markets.</p>
    <div class="socials"><span></span><span></span><span></span><span></span></div>
  </div>
  <div class="card photo" style="left:589px" role="img" aria-label="Portrait of team member Simon"><div class="label">Simon</div></div>
  <div class="card photo" style="left:803px" role="img" aria-label="Portrait of team member Paul"><div class="label">Paul SVP</div></div>
  <div class="vert" style="left:1040px;top:60px">— Our Team —</div>
</section>

<section class="partners">
  <h2 class="section-title heading" style="top:2226px">Our <span>Certified Partner</span></h2>
  <div class="dots"><span style="left:167px;top:2328px"></span><span style="left:167px;top:2350px"></span><span style="left:164px;top:2370px;width:19px;height:19px;background:#fff;border:4px solid #222"></span><span style="left:167px;top:2414px"></span><span style="left:167px;top:2436px"></span></div>
  <div class="partner" style="left:220px;top:2292px">Streamvale</div>
  <div class="partner" style="left:362px;top:2292px">Nexara</div>
  <div class="partner" style="left:504px;top:2292px"><span class="emblem"></span></div>
  <div class="partner" style="left:220px;top:2402px"><span class="emblem"></span></div>
  <div class="partner" style="left:362px;top:2402px">Brightcast</div>
  <div class="partner" style="left:504px;top:2402px"><span class="emblem"></span></div>
  <div class="cert"><span class="mark"></span><span class="brand">velmora</span></div>
  <p class="cert-note"><a href="#">Contact us</a> for details of how to become a Certified Developer Partner.</p>
</section>

<section class="contact">
  <h2 class="section-title heading" style="left:668px;top:2226px">Contact <span>Us</span></h2>
  <div class="field" style="top:2288px;height:35px">Your Name</div>
  <div class="field" style="top:2339px;height:35px">Your Email</div>
  <div class="field" style="top:2390px;height:35px">Subject</div>
  <div class="field" style="top:2441px;height:92px">Message</div>
  <div class="btn send">Send Message <span class="tri"></span></div>
</section>

<footer class="site-footer">
  <span class="copy">Copyright © 2016 Velmoramedia. All rights reserved.</span>
  <span class="follow">Follow Us:</span>
  <div class="icons"><span></span><span></span><span></span><span></span><span></span><span></span></div>
</footer>

</body>
</html>
```